Redesign current business card for food company

i would like to redesign my business card. our company is food company, our product range from chips, juices, milk and etc (mostly dried food stuff).
I want o keep same logo but , the rest is open to new design.
you can check at our website about our company www.orvelpantry.com

Target Market(s)

most of food company

Industry/Entity Type

Business

Contact Information for Business Card

I want to keep more to blue color...

Colors
3176b5
abd036

Requirements
Must have
• our old logo
Nice to have
• we do not mind to have nice material on bus card in order to accomplish nice design. for example: using spot uv, embossed and etc.

```html
<!DOCTYPE html>
<html lang="en">
<head>
<meta charset="utf-8">
<title>Orvel Business Card</title>
<link href="https://fonts.googleapis.com/css2?family=Montserrat:wght@400;500;700;800&display=swap" rel="stylesheet">
<style>
  :root {
    --indigo: #34309a;
    --cyan: #1fb3d1;
    --paper: #ffffff;
    --backdrop: #e9ebef;
    --ink-light: #ffffff;
  }
  * { box-sizing: border-box; margin: 0; padding: 0; }
  html, body {
    width: 1200px; height: 900px; overflow: hidden;
    background: var(--backdrop);
    font-family: "Montserrat", sans-serif;
  }
  .stage { position: relative; width: 1200px; height: 900px; }
  .card {
    position: absolute;
    width: 520px; height: 300px;
    background: var(--paper);
    border-radius: 18px;
    overflow: hidden;
    box-shadow: 0 10px 30px rgba(30, 30, 60, 0.18);
  }
  .card-front { left: 70px; top: 110px; }
  .card-back { left: 610px; top: 490px; }

  .wordmark {
    display: flex; align-items: center; gap: 10px;
    color: var(--indigo);
    font-weight: 800;
    letter-spacing: -2px;
    line-height: 1;
  }
  .wordmark-dot {
    width: 16px; height: 16px; border-radius: 50%;
    background: var(--indigo);
  }
  .card-front .wordmark {
    position: absolute; left: 150px; top: 95px;
    font-size: 92px;
  }
  .front-url {
    position: absolute; left: 0; bottom: 26px;
    display: flex; align-items: center; gap: 10px;
    color: var(--indigo); font-size: 17px; font-weight: 500;
  }
  .front-url-bar {
    width: 30px; height: 9px; background: var(--cyan);
  }

  .wave { position: absolute; inset: 0; width: 100%; height: 100%; }
  .card-back .wordmark {
    position: absolute; left: 34px; top: 66px;
    font-size: 70px;
  }
  .card-back .wordmark-dot { width: 12px; height: 12px; }
  .contact {
    position: absolute; right: 26px; top: 92px;
    text-align: right; color: var(--ink-light);
  }
  .contact-name { font-size: 17px; font-weight: 700; }
  .contact-title { font-size: 13px; color: var(--cyan); margin-bottom: 6px; }
  .contact-list { list-style: none; font-size: 13px; line-height: 1.45; }
  .contact-list li { display: flex; justify-content: flex-end; align-items: center; gap: 7px; }
  .contact-list svg { width: 10px; height: 10px; fill: var(--cyan); flex: none; }
  .contact-list strong { font-weight: 700; }
  .company {
    position: absolute; left: 34px; bottom: 24px;
    color: var(--ink-light); font-size: 13px; line-height: 1.35;
  }
</style>
</head>
<body>
<main class="stage">
  <section class="card card-front">
    <div class="wordmark"><span class="wordmark-dot"></span>orvel</div>
    <div class="front-url"><span class="front-url-bar"></span>www.orvelpantry.com</div>
  </section>

  <section class="card card-back">
    <svg class="wave" viewBox="0 0 520 300" preserveAspectRatio="none" aria-hidden="true">
      <path d="M0,218 C160,215 250,205 290,150 C325,98 365,62 520,60 L520,300 L0,300 Z" fill="var(--indigo)"/>
      <path d="M0,210 C160,207 242,197 282,142 C317,90 357,54 520,52" fill="none" stroke="var(--cyan)" stroke-width="4"/>
      <path d="M0,202 C160,199 234,189 274,134 C309,82 349,46 500,44" fill="none" stroke="var(--indigo)" stroke-width="3"/>
      <path d="M20,194 C160,191 226,181 266,126 C301,74 341,38 470,36" fill="none" stroke="var(--cyan)" stroke-width="2"/>
    </svg>
    <div class="wordmark"><span class="wordmark-dot"></span>orvel</div>
    <div class="contact">
      <p class="contact-name">Marco Delgrave</p>
      <p class="contact-title">President</p>
      <ul class="contact-list">
        <li>555 201 4410 <svg viewBox="0 0 10 10"><path d="M2 0.5 L4 2.5 L3 4 Q4.5 6 6 7 L7.5 6 L9.5 8 L8 9.5 Q3 9 0.5 2 Z"/></svg></li>
        <li>555 201 4427 <svg viewBox="0 0 10 10"><rect x="0" y="2" width="10" height="6" rx="1"/></svg></li>
        <li>555 738 2093 <svg viewBox="0 0 10 10"><rect x="2.5" y="0" width="5" height="10" rx="1"/></svg></li>
        <li>marco@orvelpantry.com <svg viewBox="0 0 10 10"><path d="M0 2 H10 V8 H0 Z M0 2 L5 5.5 L10 2" fill="none" stroke="var(--cyan)" stroke-width="1.2"/></svg></li>
        <li><span>www.<strong>orvelpantry</strong>.com</span> <svg viewBox="0 0 10 10"><circle cx="5" cy="5" r="4.5"/></svg></li>
      </ul>
    </div>
    <p class="company">Orvel Enterprises Corp.<br>2840 Linden Ave. Fairview CA 90417</p>
  </section>
</main>
</body>
</html>
```